Brisk Coatings business card for residential and commercial painting

A clean, professional design. Easy to read
Eye catching and elegant
Front could have some color variations
On the back of card I would like all black with signature logo

*Attached is my current business card and the items I want displayed

Contact Information for Business Card

Email, phone number, website, and owner name

Font styles to use
Serif

Requirements
Must have
• My logo with cool design and perhaps some paint splatter

```html
<!DOCTYPE html>
<html lang="en">
<head>
<meta charset="utf-8">
<title>Brisk Coatings – Business Card</title>
<link rel="stylesheet" href="https://fonts.googleapis.com/css2?family=Oswald:wght@400;500&family=Arimo:wght@400&display=swap">
<style>
  :root {
    --page-bg: #e9e7e5;
    --card-dark: #3a3a3c;
    --brand-blue: #1576be;
    --brush-tone: #5f98c9;
    --text-light: #ffffff;
    --field-white: #ffffff;
  }
  * { box-sizing: border-box; margin: 0; padding: 0; }
  html, body {
    width: 1200px; height: 900px; overflow: hidden;
    background: var(--page-bg);
  }
  .business-card {
    position: absolute; left: 100px; top: 140px;
    width: 1000px; height: 620px;
    background: var(--card-dark);
    overflow: hidden;
    box-shadow: 0 10px 30px rgba(0,0,0,0.18);
  }
  .brush-panel {
    position: absolute; left: 0; top: 0;
    width: 262px; height: 100%;
    background: linear-gradient(180deg, var(--brand-blue) 0%, var(--brush-tone) 55%, var(--brand-blue) 100%);
  }
  .brand-mark {
    position: absolute; left: 374px; top: 68px;
    display: flex; align-items: center; gap: 18px;
  }
  .brand-dot {
    width: 26px; height: 26px; border-radius: 50%;
    background: var(--brand-blue);
  }
  .brand-name {
    font-family: "Oswald", sans-serif; font-weight: 500;
    font-size: 68px; line-height: 1; letter-spacing: 1px;
    color: var(--text-light); text-transform: uppercase;
  }
  .owner {
    position: absolute; left: 374px; top: 240px;
  }
  .owner-name {
    font-family: "Oswald", sans-serif; font-weight: 400;
    font-size: 52px; line-height: 1.1; color: var(--brand-blue);
  }
  .owner-title {
    font-family: "Arimo", sans-serif; font-size: 27px;
    color: var(--text-light); margin-top: 2px;
  }
  .contact-list {
    position: absolute; left: 374px; top: 366px;
    list-style: none;
  }
  .contact-item {
    display: flex; align-items: center; gap: 16px;
    height: 36px;
    font-family: "Arimo", sans-serif; font-size: 27px;
    color: var(--text-light);
  }
  .contact-icon { width: 30px; height: 30px; flex: none; }
  .price-row {
    position: absolute; left: 374px; top: 517px;
    display: flex; align-items: center; gap: 24px;
  }
  .price-label {
    font-family: "Oswald", sans-serif; font-weight: 400;
    font-size: 40px; color: var(--brand-blue);
  }
  .price-field {
    width: 272px; height: 62px; background: var(--field-white);
  }
</style>
</head>
<body>
  <main class="business-card">
    <div class="brush-panel" role="img" aria-label="Large paintbrush illustration dripping paint on a blue panel"></div>

    <header class="brand-mark">
      <span class="brand-dot"></span>
      <span class="brand-name">Brisk Coatings</span>
    </header>

    <section class="owner">
      <h1 class="owner-name">Marco "Mo"</h1>
      <p class="owner-title">Owner-Licensed &amp; Insured</p>
    </section>

    <ul class="contact-list">
      <li class="contact-item">
        <svg class="contact-icon" viewBox="0 0 24 24" aria-hidden="true"><path fill="#1576be" d="M6.6 10.8a15 15 0 0 0 6.6 6.6l2.2-2.2c.3-.3.7-.4 1-.2 1.1.4 2.3.6 3.6.6.6 0 1 .4 1 1V20c0 .6-.4 1-1 1A17 17 0 0 1 3 4c0-.6.4-1 1-1h3.5c.6 0 1 .4 1 1 0 1.3.2 2.5.6 3.6.1.3 0 .7-.2 1z"/></svg>
        <span>93.555.0148</span>
      </li>
      <li class="contact-item">
        <svg class="contact-icon" viewBox="0 0 24 24" aria-hidden="true"><rect x="2" y="5" width="20" height="14" fill="#1576be"/><path d="M2 5l10 8 10-8" fill="none" stroke="#3a3a3c" stroke-width="1.6"/></svg>
        <span>briskcoatingstn@mail.com</span>
      </li>
      <li class="contact-item">
        <svg class="contact-icon" viewBox="0 0 24 24" aria-hidden="true"><g fill="none" stroke="#1576be" stroke-width="1.8"><circle cx="12" cy="12" r="9"/><ellipse cx="12" cy="12" rx="4" ry="9"/><path d="M3 12h18M5 7h14M5 17h14"/></g></svg>
        <span>www.briskcoatingstn.com</span>
      </li>
    </ul>

    <div class="price-row">
      <span class="price-label">Price:</span>
      <span class="price-field"></span>
    </div>
  </main>
</body>
</html>
```